Independent Statistical Consultant Business Card

I will be going out as an independent statistical consultant and need a business card. I specialize in data analysis and statistics for health care and public health

I am an Chartered Quantitative Analyst from the Coastal Numerics Federation. Would like to incorporate that logo into the design

The design should be modern with classic colors, convey accuracy, analytic creativity and responsiveness to client needs.

The name of the firm will be simply Tim Halvorsen Applied Statistical Consulting

To all designers, I want to clarify that the QMetr logo and the phrase Chartered Quantitative Analyst are not the name of the company nor the focus of the card. They are equivalent to being a Velorin Qualified Engineer (VQE) but in the area of statistics The name of the firm will be: Tim Halvorsen, Applied Statistical Consulting. I look forward to your submissions. Thanks. Tim

```html
<!DOCTYPE html>
<html lang="en">
<head>
<meta charset="utf-8">
<title>Tim Halvorsen — Applied Statistical Consulting</title>
<link rel="stylesheet" href="https://fonts.googleapis.com/css2?family=Cabin:wght@400;500&family=Tinos&display=swap">
<style>
  :root {
    --card-bg: #ffffff;
    --ink: #3f4a54;
    --mark-ink: #1c1c1e;
    --mark-light: #8b97ff;
    --mark-deep: #1440ff;
  }
  html, body {
    margin: 0;
    padding: 0;
    overflow: hidden;
    background: var(--card-bg);
  }
  .card {
    position: relative;
    width: 1200px;
    height: 697px;
    background: var(--card-bg);
    overflow: hidden;
    font-family: "Cabin", "Gill Sans", sans-serif;
    color: var(--ink);
  }
  .brand-mark {
    position: absolute;
    left: 131px;
    top: 193px;
    width: 325px;
    height: 400px;
    background: linear-gradient(90deg, var(--mark-light), var(--mark-deep));
  }
  .credential-name {
    position: absolute;
    right: 176px;
    top: 280px;
    margin: 0;
    font-family: "Cabin", "Gill Sans", sans-serif;
    font-weight: 500;
    font-size: 66px;
    line-height: 1;
    color: var(--mark-ink);
    white-space: nowrap;
  }
  .credential-title {
    position: absolute;
    right: 123px;
    top: 362px;
    margin: 0;
    font-family: "Tinos", "Times New Roman", serif;
    font-size: 18px;
    line-height: 1;
    color: var(--mark-ink);
    white-space: nowrap;
  }
  .credential-title sup {
    font-size: 8px;
    vertical-align: 8px;
  }
  .consultant-name,
  .consultant-firm,
  .consultant-phone {
    position: absolute;
    right: 125px;
    margin: 0;
    line-height: 1;
    white-space: nowrap;
  }
  .consultant-name {
    top: 408px;
    font-weight: 400;
    font-size: 66px;
    letter-spacing: 1px;
  }
  .consultant-firm {
    top: 489px;
    font-size: 40px;
  }
  .consultant-phone {
    top: 552px;
    font-size: 36px;
  }
</style>
</head>
<body>
<main class="card">
  <div class="brand-mark" role="img" aria-label="Consultancy symbol in graded blue tones"></div>

  <p class="credential-name">QMetr</p>
  <p class="credential-title">Chartered Quantitative Analyst<sup>TM</sup></p>

  <h1 class="consultant-name">TIM HALVORSEN</h1>
  <p class="consultant-firm">Applied Statistical Consulting</p>
  <p class="consultant-phone">p 000 000 0000</p>
</main>
</body>
</html>
```